KORVAL:advise Business Cards

We need a business card design for KORVAL:advise (Logo Attached), a management consultancy specialized in brand & business building.

Design should be clean, smart and a touch of innnovation without being gimmicky.

The details on the card should be:
Name: Tomas Velduren
Title: Managing Director
Address: 42 Marlowe Pier, Tarn Vessel Tower, Singapore 073926
Tel: +6285927461082
email: tv@korvaladvise.example
website: korvaladvise.example

For further background on corporate identity, please check www.korvaladvise.example
Updates

Dear all,

Many thanks for the submissions so far! I gave feedback to those designs that I prefer at this stage.

Overall I see that my preference goes into the direction that 'less is more' and 'simple is beautiful'

Please create uniqueness and standout by the simplicity and attraction of the overall concept and design.

Many thanks and please shout incase of questions!

Tomas

Industry/Entity Type

Business

```html
<!DOCTYPE html>
<html lang="en">
<head>
<meta charset="utf-8">
<title>Korval Advise Business Cards</title>
<link rel="stylesheet" href="https://fonts.googleapis.com/css2?family=Open+Sans:wght@400;600;700&display=swap">
<style>
  :root {
    --stage: #e9e7e4;
    --paper: #ffffff;
    --charcoal: #4a4a4a;
    --ink: #4d4d4d;
    --text: #333333;
    --orange: #f47a20;
    --white: #ffffff;
  }
  * { box-sizing: border-box; margin: 0; padding: 0; }
  html, body { width: 1174px; height: 1200px; overflow: hidden; }
  body {
    background: var(--stage);
    font-family: "Open Sans", Arial, sans-serif;
    position: relative;
  }
  .card {
    position: absolute;
    width: 943px;
    height: 537px;
    border-radius: 34px;
    overflow: hidden;
  }
  .card--front { left: 32px; top: 30px; background: var(--paper); border: 2px solid #3c3c3c; }
  .card--back { left: 192px; top: 612px; background: var(--charcoal); }

  .swoosh { position: absolute; inset: 0; width: 100%; height: 100%; }

  .company-name {
    position: absolute;
    left: 0; right: 0;
    text-align: center;
    font-weight: 600;
    letter-spacing: 0;
    line-height: 1;
    white-space: nowrap;
  }
  .card--front .company-name { top: 88px; font-size: 68px; color: var(--ink); }
  .card--back .company-name { top: 226px; font-size: 80px; color: var(--white); }

  .holder {
    position: absolute; left: 0; right: 0; top: 250px;
    text-align: center; font-size: 26px; color: var(--ink);
    white-space: nowrap;
  }
  .holder__name { font-weight: 700; }
  .holder__title { color: var(--orange); font-size: 22px; font-weight: 400; }

  .contact {
    position: absolute; left: 0; right: 0;
    text-align: center; font-size: 21px; color: var(--text);
    display: flex; justify-content: center; align-items: center; gap: 8px;
    white-space: nowrap;
  }
  .contact--phone { top: 316px; }
  .contact--web { top: 355px; }
  .contact svg { width: 18px; height: 18px; flex: none; }
  .contact__gap { width: 6px; }

  .address {
    position: absolute; left: 0; right: 0; top: 493px;
    text-align: center; font-size: 22px; color: var(--white);
    white-space: nowrap;
  }
  .site {
    position: absolute; left: 0; right: 0; top: 410px;
    text-align: center; font-size: 25px; color: var(--white);
    letter-spacing: 5px;
    white-space: nowrap;
  }
</style>
</head>
<body>
  <section class="card card--front" aria-label="Business card front">
    <svg class="swoosh" viewBox="0 0 943 537" preserveAspectRatio="none" aria-hidden="true">
      <path d="M0 352 Q 380 480 790 464 Q 400 480 0 376 Z" fill="var(--orange)"/>
      <path d="M0 386 Q 420 530 943 444 L943 537 L0 537 Z" fill="var(--charcoal)"/>
    </svg>
    <div class="company-name">Korval Advise</div>
    <p class="holder"><span class="holder__name">Tomas Velduren,</span> <span class="holder__title">Managing Director</span></p>
    <p class="contact contact--phone">
      <svg viewBox="0 0 24 24" aria-hidden="true"><path d="M6.6 10.8a15.1 15.1 0 0 0 6.6 6.6l2.2-2.2c.3-.3.7-.4 1-.2 1.1.4 2.3.6 3.6.6.6 0 1 .4 1 1V20c0 .6-.4 1-1 1A17 17 0 0 1 3 4c0-.6.4-1 1-1h3.5c.6 0 1 .4 1 1 0 1.3.2 2.5.6 3.6.1.3 0 .7-.2 1z" fill="none" stroke="#333" stroke-width="1.8"/></svg>
      +6285927461082
    </p>
    <p class="contact contact--web">
      <svg viewBox="0 0 24 24" aria-hidden="true"><path d="M2 9l10-6 10 6v12H2z" fill="#333"/><path d="M2 9l10 7 10-7" fill="none" stroke="#fff" stroke-width="1.6"/></svg>
      tv@korvaladvise.example
      <span class="contact__gap"></span>
      <svg viewBox="0 0 24 24" aria-hidden="true"><circle cx="12" cy="12" r="10" fill="none" stroke="#333" stroke-width="1.8"/><ellipse cx="12" cy="12" rx="4.5" ry="10" fill="none" stroke="#333" stroke-width="1.5"/><path d="M2 12h20M4 7h16M4 17h16" stroke="#333" stroke-width="1.3"/></svg>
      www.korvaladvise.example
    </p>
    <p class="address">42 Marlowe Pier, Tarn Vessel Tower, Singapore 073926</p>
  </section>

  <section class="card card--back" aria-label="Business card back">
    <div class="company-name">Korval Advise</div>
    <p class="site">www.korvaladvise.example</p>
  </section>
</body>
</html>
```